QRV Advisors needs a web site

We need a web site for www.qrvadvisors-example.com. QRV is a mergers and acquisition consulting company that focuses our buyer and seller services on logistics companies. We help put companies together, and help with legal and financial due diligence. We want the web site to express our service and show the logistics components. We want personalized images versus pictures of trucks and airplanes.

Our new logo uses Burgandy and grey colors. Image attached. We are not in to bold, big letters...classy, artistic, low key preferred. Confidentiality, experience, professional are what we want to express on the site.

All we expect for the first part of this project is a home page, and one subpage.  We are budgeting other funds for the technical aspects of the web site

Reason: All that I'm seeing so far is trucks, forklifts and planes. We are a legal mergers and acquisitions firm that focus on logistics. I like some of the images to say logistics, but really want it say legal, financial, and putting companies together. Will pay extra for the sub page if someone can impress us with a home page.

Reason: Swamped with another project at the moment...will work on this over the weekend and provide designer feedback and select final design by Tuesday

```html
<!DOCTYPE html>
<html lang="en">
<head>
<meta charset="utf-8">
<title>QRV Advisors</title>
<link href="https://fonts.googleapis.com/css2?family=Open+Sans:wght@400;600;700&family=Roboto+Condensed:wght@400;700&family=Arvo:wght@700&display=swap" rel="stylesheet">
<style>
:root{
  --burgundy:#a6073a;
  --burgundy-dark:#8c0630;
  --ink:#3b3b3b;
  --grey:#6b6b6b;
  --light:#f1f1f1;
  --band:#3e3e3e;
  --band-dark:#2e2e2e;
  --rule:#c8c8c8;
  --white:#ffffff;
}
*{box-sizing:border-box;margin:0;padding:0}
html,body{width:1004px;height:1200px;overflow:hidden}
body{font-family:"Open Sans",Arial,sans-serif;color:var(--ink);background:var(--white);position:relative}
.abs{position:absolute}

/* header */
.site-header{left:0;top:0;width:1004px;height:122px;background:linear-gradient(#f3f3f3,#ececec);border-top:6px solid #5a5a5a}
.brand{left:116px;top:44px;font-family:"Open Sans",sans-serif;font-weight:600;font-size:30px;color:var(--burgundy);letter-spacing:1px;display:flex;align-items:center;gap:10px}
.brand-mark{width:14px;height:14px;background:var(--burgundy)}
.call{left:744px;top:20px;display:flex;align-items:center;gap:8px}
.call-icon{width:28px;height:28px;border:2px solid var(--burgundy);border-radius:50%;display:flex;align-items:center;justify-content:center}
.call-label{font-size:11px;color:var(--ink);line-height:13px}
.call-number{font-size:18px;font-weight:700;color:var(--burgundy);line-height:20px}
.main-nav{left:440px;top:74px;display:flex;gap:16px;font-size:11.5px;color:var(--grey)}
.main-nav a{color:inherit;text-decoration:none;border-top:1px solid var(--rule);border-bottom:1px solid var(--rule);padding:4px 2px;position:relative}
.main-nav a.active{color:var(--burgundy);font-weight:700}
.main-nav a.active::before{content:"";position:absolute;left:50%;top:-1px;margin-left:-4px;border:4px solid transparent;border-top-color:#555}

/* hero */
.hero{left:0;top:125px;width:1004px;height:371px;background:linear-gradient(100deg,#c9b9aa 0%,#e9ecef 30%,#d4d9de 55%,#3a3f4b 75%,#c7b4a3 100%)}
.hero-arrow{width:38px;height:38px;border-radius:50%;background:#222;border:3px solid #777;display:flex;align-items:center;justify-content:center;top:280px}
.hero-caption{left:557px;top:378px;width:447px;height:72px;background:rgba(40,40,40,.65);font-family:"Arvo",serif;font-size:24px;color:var(--white);line-height:34px;padding:2px 0 0 50px;text-shadow:1px 1px 2px #000;letter-spacing:.5px}

/* services */
.services{left:0;top:496px;width:1004px;height:226px;background:linear-gradient(var(--band),var(--band-dark));border-top:3px solid #555}
.service{width:170px;text-align:center;top:24px}
.service-badge{width:118px;height:118px;margin:0 auto;border-radius:50%;background:var(--burgundy);display:flex;align-items:center;justify-content:center}
.service h3{font-family:"Roboto Condensed",sans-serif;font-weight:700;font-size:15px;color:var(--white);margin-top:12px}
.service p{font-size:10px;color:#e6e6e6;line-height:15px;margin-top:5px}
.band-arrow{top:66px}

/* content */
.section-title{font-family:"Roboto Condensed",sans-serif;font-weight:700;font-size:17px;color:#666;top:746px;border-bottom:1px dashed #aaa;padding-bottom:6px}
.section-title b{color:var(--burgundy)}
.about-photo{left:118px;top:785px;width:235px;height:102px;border:4px solid var(--burgundy);background:linear-gradient(90deg,#3b3c44,#d8cfc2 45%,#f1ede6 60%,#4a4a55)}
.about-text{left:119px;top:897px;width:235px;font-size:10.3px;line-height:15.4px}
.read-more{font-size:10px;font-weight:700;color:var(--burgundy);text-decoration:none}
.news-item{left:386px;width:234px;border-bottom:1px dotted #ccc;height:76px}
.news-date{font-size:10px;color:var(--burgundy)}
.news-text{font-size:10px;line-height:15.5px;letter-spacing:.6px;margin-top:2px}
.news-item .read-more{position:absolute;right:2px;top:51px}
.form-label{left:654px;font-size:11px}
.form-field{left:709px;width:177px;height:18px;border:1px solid #bbb;background:var(--white)}
.submit{left:709px;top:972px;width:87px;height:21px;background:var(--burgundy);color:var(--white);font-family:"Roboto Condensed",sans-serif;font-weight:700;font-size:13px;text-align:center;line-height:21px}
.divider{width:1px;background:linear-gradient(transparent,#ddd,transparent);top:740px;height:290px}

/* footer */
.site-footer{left:0;top:1031px;width:1004px;height:169px;background:var(--burgundy);border-top:4px solid #6c6c6c;color:var(--white)}
.foot-title{font-family:"Roboto Condensed",sans-serif;font-weight:700;font-size:12.5px;top:18px;border-bottom:1px dashed rgba(255,255,255,.6);padding-bottom:5px}
.quick-links{left:118px;top:50px;list-style:none;font-size:10px;line-height:18.5px}
.quick-links li::before{content:"›";margin-right:8px}
.foot-contact{font-size:10px;line-height:14px}
.foot-sep{width:1px;background:rgba(255,255,255,.3);top:20px;height:140px}
.newsletter-text{left:513px;top:50px;width:180px;font-size:10px;line-height:15px}
.email-field{left:512px;top:83px;width:169px;height:19px;background:var(--white);border-radius:2px;font-size:10px;color:#888;padding:2px 0 0 26px}
.subscribe{left:513px;top:113px;width:67px;height:20px;background:#4a4a4a;font-weight:700;font-size:11px;text-align:center;line-height:20px}
.foot-brand{left:709px;top:14px;font-family:"Open Sans",sans-serif;font-weight:600;font-size:52px;color:#8e8e8e;letter-spacing:6px;line-height:60px}
.socials{left:766px;top:85px;display:flex;gap:9px}
.socials span{width:20px;height:20px;border-radius:3px;background:#4d7bc2}
.copyright{left:710px;top:119px;width:184px;text-align:center;font-size:10px;line-height:15px}
</style>
</head>
<body>

<header class="site-header abs">
  <div class="brand abs"><span class="brand-mark"></span>QRV Advisors</div>
  <div class="call abs">
    <div class="call-icon">
      <svg width="14" height="14" viewBox="0 0 24 24"><path d="M6 2l4 4-2 3c1 3 4 6 7 7l3-2 4 4-3 4C10 21 3 14 2 5z" fill="none" stroke="#a6073a" stroke-width="2"/></svg>
    </div>
    <div><div class="call-label">Call Us Today</div><div class="call-number">555 014 2290</div></div>
  </div>
  <nav class="main-nav abs">
    <a class="active">Home</a><a>About Us</a><a>Consulting Services</a><a>News &amp; Events</a><a>FAQ's</a><a>Contact Us</a>
  </nav>
</header>

<section class="hero abs" role="img" aria-label="Photo of advisors smiling in a business meeting"></section>
<div class="hero-arrow abs" style="left:119px"><svg width="12" height="16"><path d="M9 2L3 8l6 6" stroke="#fff" stroke-width="2" fill="none"/></svg></div>
<div class="hero-arrow abs" style="left:846px"><svg width="12" height="16"><path d="M3 2l6 6-6 6" stroke="#fff" stroke-width="2" fill="none"/></svg></div>
<div class="hero-caption abs">We Are A Technology<br>Consulting Company.</div>

<section class="services abs">
  <svg class="band-arrow abs" style="left:94px" width="16" height="28"><path d="M13 2L3 14l10 12" stroke="#999" stroke-width="2" fill="none"/></svg>
  <svg class="band-arrow abs" style="left:890px" width="16" height="28"><path d="M3 2l10 12L3 26" stroke="#999" stroke-width="2" fill="none"/></svg>

  <div class="service abs" style="left:129px">
    <div class="service-badge"><svg width="64" height="64" viewBox="0 0 64 64" fill="#fff"><rect x="6" y="34" width="5" height="22"/><rect x="14" y="28" width="5" height="28"/><rect x="22" y="38" width="5" height="18"/><rect x="30" y="32" width="5" height="24"/><rect x="38" y="42" width="5" height="14"/><rect x="4" y="56" width="42" height="3"/><circle cx="40" cy="20" r="10" fill="none" stroke="#fff" stroke-width="4"/><path d="M46 27l12 12" stroke="#fff" stroke-width="5"/></svg></div>
    <h3>Business Analysis</h3><p>Lorem ipsum dolor sit ameteuis tincidunt ut laoreet amte</p>
  </div>
  <div class="service abs" style="left:321px">
    <div class="service-badge"><svg width="72" height="50" viewBox="0 0 72 50" fill="#fff"><circle cx="14" cy="14" r="7"/><circle cx="36" cy="11" r="8"/><circle cx="58" cy="14" r="7"/><path d="M2 46c0-14 4-22 12-22s12 8 12 22z"/><path d="M22 48c0-16 5-26 14-26s14 10 14 26z"/><path d="M46 46c0-14 4-22 12-22s12 8 12 22z"/></svg></div>
    <h3>Business Intelligence</h3><p>Lorem ipsum dolor sit ameteuis tincidunt ut laoreet amte</p>
  </div>
  <div class="service abs" style="left:513px">
    <div class="service-badge"><svg width="50" height="76" viewBox="0 0 50 76" fill="#fff"><path d="M25 0l14 28h-8v10c0 12 10 20 19 38H36c-4-9-11-16-11-22 0 6-7 13-11 22H0c9-18 19-26 19-38V28h-8z"/></svg></div>
    <h3>Mergers</h3><p>Lorem ipsum dolor sit ameteuis tincidunt ut laoreet amte</p>
  </div>
  <div class="service abs" style="left:705px">
    <div class="service-badge"><svg width="74" height="60" viewBox="0 0 74 60" fill="#fff"><path d="M48 2l24 20-24 20V30H32V14h16z"/><path d="M26 18L2 38l24 20V46h16V30H26z"/></svg></div>
    <h3>Acquisition</h3><p>Lorem ipsum dolor sit ameteuis tincidunt ut laoreet amte</p>
  </div>
</section>

<h2 class="section-title abs" style="left:119px;width:234px"><b>ABOUT</b> COMPANY</h2>
<div class="about-photo abs" role="img" aria-label="Photo of the advisory team"></div>
<p class="about-text abs">QRV assists business owners within the logistics industry to implement growth and exit strategies. We offer business planning and merger and acquisition(M&amp;A) advisory services. QRV services are offered by industry executives with extensive M&amp;A experience..</p>
<a class="read-more abs" style="left:294px;top:983px">Read More »</a>

<div class="divider abs" style="left:368px"></div>
<h2 class="section-title abs" style="left:386px;width:234px"><b>NEWS &amp;</b> EVENTS</h2>
<article class="news-item abs" style="top:784px"><div class="news-date">8-10-2014 | By Admin</div><p class="news-text">Lorem ipsum dolor sit amet, consectetuer adipiscing elit, sed diam...</p><a class="read-more">Read More »</a></article>
<article class="news-item abs" style="top:860px"><div class="news-date">8-10-2014 | By Admin</div><p class="news-text">Lorem ipsum dolor sit amet, consectetuer adipiscing elit, sed diam...</p><a class="read-more">Read More »</a></article>
<article class="news-item abs" style="top:938px;border:0"><div class="news-date">8-10-2014 | By Admin</div><p class="news-text">Lorem ipsum dolor sit amet, consectetuer adipiscing elit, sed diam...</p><a class="read-more">Read More »</a></article>

<div class="divider abs" style="left:635px"></div>
<h2 class="section-title abs" style="left:652px;width:234px"><b>CONTACT</b> US</h2>
<span class="form-label abs" style="top:787px">Name</span><div class="form-field abs" style="top:785px"></div>
<span class="form-label abs" style="top:822px">Phone</span><div class="form-field abs" style="top:820px"></div>
<span class="form-label abs" style="top:857px">Email</span><div class="form-field abs" style="top:855px"></div>
<span class="form-label abs" style="top:892px">Message</span><div class="form-field abs" style="top:890px;height:58px"></div>
<div class="submit abs">SUBMIT</div>

<footer class="site-footer abs">
  <h4 class="foot-title abs" style="left:118px;width:111px">QUICK LINKS</h4>
  <ul class="quick-links abs"><li>Home</li><li>About Us</li><li>Consulting Services</li><li>News &amp; Events</li><li>FAQ's</li><li>Contact Us</li></ul>
  <div class="foot-sep abs" style="left:245px"></div>

  <h4 class="foot-title abs" style="left:272px;width:190px">CONTACT US</h4>
  <svg class="abs" style="left:274px;top:50px" width="13" height="18" viewBox="0 0 13 18"><path d="M6.5 0A6 6 0 0 0 .5 6c0 5 6 12 6 12s6-7 6-12a6 6 0 0 0-6-6z" fill="#fff"/><circle cx="6.5" cy="6" r="2.2" fill="#a6073a"/></svg>
  <p class="foot-contact abs" style="left:301px;top:50px;width:180px">Lorem ipsum dolor sit ameteuismo tincidunt ut laoreet dolore my amte,</p>
  <svg class="abs" style="left:274px;top:91px" width="14" height="14" viewBox="0 0 24 24"><path d="M6 2l4 4-2 3c1 3 4 6 7 7l3-2 4 4-3 4C10 21 3 14 2 5z" fill="#fff"/></svg>
  <p class="foot-contact abs" style="left:301px;top:92px">555-014-2290</p>
  <svg class="abs" style="left:273px;top:124px" width="16" height="11" viewBox="0 0 16 11"><rect width="16" height="11" fill="#fff"/><path d="M0 0l8 6 8-6" stroke="#a6073a" fill="none"/></svg>
  <p class="foot-contact abs" style="left:301px;top:122px">info@qrvadvisors-example.com</p>
  <div class="foot-sep abs" style="left:489px"></div>

  <h4 class="foot-title abs" style="left:513px;width:179px">NEWSLETTER</h4>
  <p class="newsletter-text abs">Subscribe to our newsletter to receive our special offers , discounts &amp; more.</p>
  <div class="email-field abs"><svg class="abs" style="left:7px;top:5px" width="13" height="9"><rect width="13" height="9" fill="#ccc"/><path d="M0 0l6.5 5L13 0" stroke="#fff" fill="none"/></svg>your e-mail address</div>
  <div class="subscribe abs">Subscribe</div>

  <div class="foot-brand abs">QRV</div>
  <div class="socials abs"><span></span><span style="background:#3fa7dc"></span><span style="background:#2a79b5"></span></div>
  <p class="copyright abs">© 2014 qrvadvisors-example.<br>All Rights Reserved</p>
</footer>

</body>
</html>
```